Book Cover for Harbor Holiday Voyage Needed!

Marble Finch Press needs a cover for a novella. We will need an ebook cover and print wrap. We need to stay with the brand we have as indicated by the files attached. Take a look for the brand and style we are looking for.
Here are the specifics:
Title (subject to change): Seaside Wish
Subtitle: A Christmas Novella
Series Name: The Lagoon Pages Love Series (Book 3.5)
Author: Mira Calloway

Target Market(s)

Romance readers

Industry/Entity Type

Entertainment Industry

Font styles to use
Other font styles liked:
• NovitoNova - Title, Neumann - Subtitle

Colors
3276b5
33a6d7
33b8a4
abd036
fbee3d
ffc214

Requirements
Must have
• Please take a look at the other three covers to stay on brand and for inspiration
Nice to have
• Possibly something with a criuse ship.
Should not have
• Not looking for "real" images or depictions. We want a scene with bright colors same as the previous books but with a bit of a casual feel.

```html
<!DOCTYPE html>
<html lang="en">
<head>
<meta charset="utf-8">
<title>Seaside Wish — Book Cover</title>
<link rel="stylesheet" href="https://fonts.googleapis.com/css2?family=Antonio:wght@100;200&family=Parisienne&family=Marcellus&family=Libre+Baskerville&display=swap">
<style>
  :root {
    --page: #ffffff;
    --sky-deep: #2f74c4;
    --sky-mid: #4f9ad9;
    --cloud: #dfeef6;
    --sea-light: #8fe0e2;
    --sea-turquoise: #33b8c4;
    --sand: #f4ece6;
    --frond: #2e6b3a;
    --ribbon: #4fb1e3;
    --ribbon-edge: #e6b84a;
    --navy: #1d2d5c;
    --ink-dark: #1a1f2e;
    --title-white: #ffffff;
    --title-edge: #2b3a58;
  }
  * { box-sizing: border-box; margin: 0; padding: 0; }
  html, body {
    width: 1000px;
    height: 1200px;
    overflow: hidden;
    background: var(--page);
  }
  .canvas {
    position: relative;
    width: 1000px;
    height: 1200px;
    background: var(--page);
  }
  .cover {
    position: absolute;
    left: 261px;
    top: 219px;
    width: 477px;
    height: 762px;
    overflow: hidden;
  }
  .cover-scene {
    position: absolute;
    inset: 0;
    background:
      radial-gradient(ellipse 60% 30% at 85% 8%, rgba(46,107,58,0.85), rgba(46,107,58,0) 70%),
      linear-gradient(180deg,
        var(--sky-deep) 0%,
        var(--sky-mid) 30%,
        var(--cloud) 46%,
        var(--cloud) 55%,
        var(--sea-turquoise) 66%,
        var(--sea-light) 82%,
        var(--sand) 100%);
  }
  .series-ribbon {
    position: absolute;
    left: 30px;
    top: 62px;
    width: 420px;
    height: 30px;
    transform: rotate(-2deg);
  }
  .series-ribbon svg { position: absolute; inset: 0; }
  .series-name {
    position: absolute;
    inset: 0;
    display: flex;
    align-items: center;
    justify-content: center;
    font-family: "Libre Baskerville", serif;
    font-size: 14px;
    color: var(--navy);
    white-space: nowrap;
  }
  .title {
    position: absolute;
    left: 0;
    width: 100%;
    text-align: center;
    font-family: "Antonio", sans-serif;
    font-weight: 100;
    color: var(--title-white);
    line-height: 1;
    transform-origin: top center;
    text-shadow:
      1px 1px 0 var(--title-edge),
      -1px 1px 0 var(--title-edge),
      1px -1px 0 var(--title-edge),
      -1px -1px 0 var(--title-edge),
      2px 3px 4px rgba(0,0,0,0.35);
  }
  .title-line-one {
    top: 162px;
    font-size: 82px;
    letter-spacing: 2px;
    transform: scaleY(1.4);
  }
  .title-line-two {
    top: 258px;
    font-size: 160px;
    letter-spacing: 4px;
    transform: scaleY(1.45);
  }
  .subtitle {
    position: absolute;
    left: 0;
    top: 536px;
    width: 100%;
    text-align: center;
    font-family: "Parisienne", cursive;
    font-size: 36px;
    line-height: 1;
    color: var(--navy);
    letter-spacing: 1px;
  }
  .author {
    position: absolute;
    left: 0;
    top: 670px;
    width: 100%;
    text-align: center;
    font-family: "Marcellus", serif;
    font-size: 31px;
    line-height: 1.2;
    letter-spacing: 5px;
    color: var(--ink-dark);
    text-transform: uppercase;
  }
</style>
</head>
<body>
  <main class="canvas">
    <section class="cover">
      <div class="cover-scene" role="img" aria-label="Bright tropical beach scene seen from above: blue sky with white clouds, palm fronds at the upper right, a white sand spit and turquoise lagoon with small boats"></div>

      <div class="series-ribbon">
        <svg width="420" height="30" viewBox="0 0 420 30" aria-hidden="true">
          <rect x="0" y="2" width="420" height="26" fill="var(--ribbon)"/>
          <line x1="0" y1="2" x2="420" y2="2" stroke="var(--ribbon-edge)" stroke-width="2"/>
          <line x1="0" y1="28" x2="420" y2="28" stroke="var(--ribbon-edge)" stroke-width="2"/>
        </svg>
        <p class="series-name">The Lagoon Pages Love Series (Book 3.5)</p>
      </div>

      <h1>
        <span class="title title-line-one">SEASIDE</span>
        <span class="title title-line-two">WISH</span>
      </h1>

      <p class="subtitle">A Christmas Novella...</p>
      <p class="author">Mira Calloway</p>
    </section>
  </main>
</body>
</html>
```